Exciting adult social quiz app needs awesome modern design

A new and exciting app for couples/sexual partners is in the making. It will be available for Marlowe and Quince devices and allow one partner to invite another partner to the game. The partners will answer questions about their sexual desires and needs and then try to guess what the other one answered.

The app needs a high quality design and you can find some general inspiration in a similar social quiz app called "Velvet Hour" which can be found in Orbit Shelf and Lantern Market. I like some of the basic layouts of this app.

The design should be classy and have a theme that matches the app subject. This is a sexual get-to-know-each-other-app and not a "porn app". I imagine colors might be black and red (not a requirement) and perhaps have some structures, pictures or backgrounds showing a bit of skin. It's important that the game can be accessed by players in the public space (e.g. in a bus, car etc.) without surroundings thinking it's a sex/porn game - but also important that it's exciting in a kind of sexual way. So try to find a fine line.

As the app is for both genders, the design should accommodate this.

Please see app mockups in the attached PDF.

Initially, please show design proposals for screens 13, 16 and 23.
Please notice that screen 16 doesn't have to be exactly those 2 bars - please make some alternative score comparison graphic in your proposal.

Looking forward to seeing your proposal soon!

Target Market(s)

Couples between 18 and 50

Industry/Entity Type

Adult

Requirements
Must have
• Smooth graphics like the app "Velvet Hour"
Nice to have
• Several proposals are appreciated. Perhaps you can show your proposals with different colors and object placements so that I can see some different options.

```html
<!DOCTYPE html>
<html lang="en">
<head>
<meta charset="utf-8">
<title>Round 1 – Time to collect</title>
<link href="https://fonts.googleapis.com/css2?family=Arimo:wght@700&family=Figtree:wght@600;700;800&display=swap" rel="stylesheet">
<style>
  :root {
    --page-bg: #1a1a1a;
    --screen-red: #e32f30;
    --glow-yellow: #ffd15a;
    --glow-orange: #f79a2a;
    --glow-deep: #ea5a2c;
    --title-black: #0c0c0c;
    --subtitle-grey: #c9c6c4;
    --reward-orange: #f5a21f;
    --button-top: #ffc21a;
    --button-bottom: #f29a0c;
    --button-text: #7a1408;
    --slider-track: #111111;
    --slider-edge: #5a5a5a;
    --heart-red: #d4141b;
  }
  * { margin: 0; padding: 0; box-sizing: border-box; }
  html, body {
    width: 674px; height: 1200px; overflow: hidden;
    background: var(--page-bg);
  }
  .screen {
    position: absolute; left: 0; top: 47px;
    width: 674px; height: 1106px;
    background: var(--screen-red);
    overflow: hidden;
    font-family: "Figtree", Arial, sans-serif;
  }
  .sunset-scene {
    position: absolute; left: 0; right: 0; bottom: 0; height: 560px;
    background:
      radial-gradient(circle at 66% 44%, #fff2a8 0 70px, var(--glow-yellow) 90px, transparent 150px),
      radial-gradient(ellipse 60% 55% at 50% 62%, var(--glow-orange) 0%, rgba(238,110,40,0.8) 45%, rgba(227,47,48,0) 100%),
      linear-gradient(to bottom, rgba(227,47,48,0) 0%, rgba(200,40,30,0.35) 100%);
  }
  .round-title {
    position: absolute; top: 18px; left: 0; width: 100%;
    text-align: center;
    font-family: "Arimo", Arial, sans-serif; font-weight: 700;
    font-size: 80px; line-height: 1;
    color: var(--title-black);
  }
  .collect-heading {
    position: absolute; top: 184px; left: 0; width: 100%;
    text-align: center; padding-left: 30px;
    font-weight: 800; font-size: 52px; line-height: 1;
    color: var(--subtitle-grey);
  }
  .reward-list { list-style: none; }
  .reward {
    position: absolute; left: 37px;
    font-weight: 700; font-size: 35px; line-height: 41px;
    color: var(--reward-orange);
  }
  .reward--oral { top: 318px; }
  .reward--naked-home { top: 399px; }
  .reward--back-massage { top: 522px; }
  .reward--foot-massage { top: 603px; }
  .scroll-slider {
    position: absolute; left: 618px; top: 368px; width: 28px; height: 258px;
    border-radius: 14px;
    background: linear-gradient(to right, var(--slider-edge), var(--slider-track) 35%, var(--slider-track) 65%, var(--slider-edge));
    box-shadow: 0 0 0 2px #2a2a2a;
  }
  .scroll-knob {
    position: absolute; left: 605px; top: 403px; width: 54px; height: 50px;
  }
  .continue-button {
    position: absolute; left: 243px; top: 908px; width: 201px; height: 43px;
    border: 1px solid #d27a05; border-radius: 3px;
    background: linear-gradient(to bottom, var(--button-top), var(--button-bottom));
    color: var(--button-text);
    font-weight: 700; font-size: 20px; line-height: 41px; text-align: center;
  }
</style>
</head>
<body>
  <main class="screen">
    <div class="sunset-scene" role="img" aria-label="Sunset scene with a silhouetted couple, a seated man and a dancing woman, in front of a glowing sun"></div>

    <h1 class="round-title">ROUND 1</h1>
    <h2 class="collect-heading">Time to collect !</h2>

    <ul class="reward-list">
      <li class="reward reward--oral">Oral... Tonight !</li>
      <li class="reward reward--naked-home">Be naked when I come<br>home tomorrow</li>
      <li class="reward reward--back-massage">Naked back massage with oil</li>
      <li class="reward reward--foot-massage">Naked foot massage</li>
    </ul>

    <div class="scroll-slider"></div>
    <svg class="scroll-knob" viewBox="0 0 54 50" aria-hidden="true">
      <defs>
        <radialGradient id="heartShine" cx="35%" cy="30%" r="70%">
          <stop offset="0" stop-color="#ff6b6b"/>
          <stop offset="1" stop-color="#b30d12"/>
        </radialGradient>
      </defs>
      <path d="M27 47 C10 34 2 25 2 15 C2 7 8 2 15 2 C20 2 24 5 27 9 C30 5 34 2 39 2 C46 2 52 7 52 15 C52 25 44 34 27 47 Z"
            fill="url(#heartShine)" stroke="#fff" stroke-width="2"/>
    </svg>

    <div class="continue-button">Continue &gt;&gt;</div>
  </main>
</body>
</html>
```